Business Cards Needed for Innovative Healthcare Marketing Company

We are a marketing company focused on healthcare. Our company is all about rebranding yourself renewing your image and generating results. The phoenix stands for "reborn" or "rising" which we provide new brands for our clients we take their old brands and renew it with creativity and innovation. I am looking for a business card with color dimension. I have attached an example of a card I think has the look and feel of what I am trying to accomplish. I like that the card example has black and grey font colors, I like the font placement and the small logo, I really like the use of the colors on the right those are the colors of my logo. My logo is phoenix so maybe incorporating flames similar to that design. I would like the back a solid color maybe red with an opaque version of the logo and website. As a marketing company I am always open to creative liberty!

Target Market(s)

Doctors and business professionals.

Industry/Entity Type

Marketing

Contact Information for Business Card

Valcorne Health Care Marketing
Marla Tenwick- CEO
#(512)638-2974
email-marla@valcorne.com
website- valcorne.com

Font styles to use
Sans Serif

Colors
ec1f27
f37122
ffc214
fbed22
fbf289
f04a50

Requirements
Must have
• The logo and required information
Nice to have
• icons by the information
Should not have
• child like font

```html
<!DOCTYPE html>
<html lang="en">
<head>
<meta charset="utf-8">
<title>Valcorne Health Care Marketing – Business Card</title>
<link rel="stylesheet" href="https://fonts.googleapis.com/css2?family=Josefin+Sans:wght@300&family=Open+Sans:wght@400;600;700&display=swap">
<style>
  :root {
    --page: #ecebea;
    --frost: #f7f5f4;
    --wine: #9e1b2c;
    --wine-soft: rgba(158, 27, 44, 0.16);
    --mark: #f37122;
    --band-top: #f59a24;
    --band-mid: #e8651f;
    --band-bottom: #c23226;
    --white: #ffffff;
  }
  * { box-sizing: border-box; margin: 0; padding: 0; }
  html, body { width: 1200px; height: 900px; overflow: hidden; }
  body {
    position: relative;
    background: var(--page);
    font-family: "Open Sans", Arial, sans-serif;
  }
  .card {
    position: absolute;
    width: 556px;
    height: 343px;
    background: var(--frost);
    box-shadow: 0 8px 24px rgba(0, 0, 0, 0.12);
    overflow: hidden;
  }
  .card--front { left: 238px; top: 62px; }
  .card--back  { left: 460px; top: 518px; }

  .card__band {
    position: absolute;
    left: 0; right: 0; bottom: 0;
    height: 157px;
    background: linear-gradient(180deg, var(--band-top) 0%, var(--band-mid) 45%, var(--band-bottom) 100%);
  }

  .brand {
    position: absolute;
    left: 80px;
    top: 36px;
    display: flex;
    align-items: flex-start;
  }
  .brand__dot {
    width: 62px; height: 62px;
    border-radius: 50%;
    background: var(--mark);
    margin-top: 12px;
    margin-right: 40px;
  }
  .brand__text { width: 290px; }
  .brand__name {
    font-family: "Josefin Sans", "Open Sans", sans-serif;
    font-weight: 300;
    font-size: 50px;
    letter-spacing: 1px;
    line-height: 1;
    color: var(--wine);
    padding-top: 14px;
  }
  .brand__rule {
    height: 1px;
    background: var(--wine);
    opacity: 0.6;
    margin: 16px 0 8px;
  }
  .brand__tagline {
    font-family: "Josefin Sans", "Open Sans", sans-serif;
    font-weight: 300;
    font-size: 19px;
    letter-spacing: 1.3px;
    color: var(--wine);
    white-space: nowrap;
  }

  .person {
    position: absolute;
    right: 310px;
    top: 60px;
    text-align: right;
    color: var(--white);
  }
  .person__name { font-weight: 700; font-size: 17px; line-height: 22px; }
  .person__role { font-size: 15px; line-height: 22px; }

  .contact {
    position: absolute;
    left: 272px;
    top: 55px;
    list-style: none;
    color: var(--white);
    font-size: 14px;
  }
  .contact__item {
    display: flex;
    align-items: center;
    height: 20px;
  }
  .contact__icon { width: 11px; height: 11px; margin-right: 9px; fill: var(--white); }

  .back-mark {
    position: absolute;
    left: 0; right: 0;
    top: 40px;
    text-align: center;
  }
  .back-mark__name {
    font-family: "Josefin Sans", "Open Sans", sans-serif;
    font-weight: 300;
    font-size: 50px;
    letter-spacing: 1px;
    color: var(--wine-soft);
    padding-top: 14px;
  }
  .back-mark__rule {
    width: 290px; height: 1px;
    margin: 14px auto 8px;
    background: var(--wine-soft);
  }
  .back-mark__tagline {
    font-family: "Josefin Sans", "Open Sans", sans-serif;
    font-weight: 300;
    font-size: 19px;
    letter-spacing: 1.3px;
    color: var(--wine-soft);
  }
  .back-site {
    position: absolute;
    left: 0; right: 0;
    top: 64px;
    text-align: center;
    color: var(--white);
    font-size: 20px;
  }
</style>
</head>
<body>

<section class="card card--front">
  <div class="brand">
    <div class="brand__dot"></div>
    <div class="brand__text">
      <div class="brand__name">VALCORNE</div>
      <div class="brand__rule"></div>
      <div class="brand__tagline">HEALTHCARE MARKETING</div>
    </div>
  </div>
  <div class="card__band">
    <div class="person">
      <div class="person__name">Marla Tenwick</div>
      <div class="person__role">CEO</div>
    </div>
    <ul class="contact">
      <li class="contact__item">
        <svg class="contact__icon" viewBox="0 0 24 24"><path d="M6.6 10.8a15 15 0 0 0 6.6 6.6l2.2-2.2a1 1 0 0 1 1-.25 11.4 11.4 0 0 0 3.6.57 1 1 0 0 1 1 1V20a1 1 0 0 1-1 1A17 17 0 0 1 3 4a1 1 0 0 1 1-1h3.5a1 1 0 0 1 1 1c0 1.25.2 2.45.57 3.57a1 1 0 0 1-.25 1z"/></svg>
        (512)638-2974
      </li>
      <li class="contact__item">
        <svg class="contact__icon" viewBox="0 0 24 24"><path d="M2 5h20v14H2z M2 5l10 8 10-8" stroke="#e8651f" stroke-width="1.5"/></svg>
        marla@valcorne.com
      </li>
      <li class="contact__item">
        <svg class="contact__icon" viewBox="0 0 24 24"><circle cx="12" cy="12" r="10"/><path d="M12 2a15 10 0 0 0 0 20M2 12h20" stroke="#e8651f" stroke-width="1.5" fill="none"/></svg>
        valcorne.com
      </li>
    </ul>
  </div>
</section>

<section class="card card--back">
  <div class="back-mark">
    <div class="back-mark__name">VALCORNE</div>
    <div class="back-mark__rule"></div>
    <div class="back-mark__tagline">HEALTHCARE MARKETING</div>
  </div>
  <div class="card__band">
    <div class="back-site">valcorne.com</div>
  </div>
</section>

</body>
</html>
```